Company Mission & Values Poster

I'd like an A2 Portrait Poster displaying our company's Mission & Values.
See our website for our logo, fonts, mission & values.
https://valdintor.com.au/

Our Mission: Creating homes for abundant life
Values: Love, Thinking, Team, Zoe.

Some ideas to consider:
Mission as the Headline then
A logo for each of the 4 Values and the words

Target Market(s)

Myself & my team

Industry/Entity Type

Real Estate

Font styles to use
Other font styles liked:
• Company fonts as seen on our website

```html
<!DOCTYPE html>
<html lang="en">
<head>
<meta charset="utf-8">
<title>Valdintor – Mission &amp; Values Poster</title>
<link rel="stylesheet" href="https://fonts.googleapis.com/css2?family=Jost:wght@400;500&family=Playfair+Display:ital,wght@0,500;1,400&display=swap">
<style>
  :root {
    --backdrop: #bdbec0;
    --paper: #f4f4f2;
    --forest: #0f3a2e;
    --forest-ink: #123a30;
    --chalk: #f3f3ef;
    --bulb: #e98a12;
    --heart: #e3262c;
    --team: #e0262c;
    --smile: #f5c331;
  }
  * { margin: 0; padding: 0; box-sizing: border-box; }
  html, body {
    width: 975px; height: 1200px; overflow: hidden;
    background: var(--backdrop);
  }
  .canvas { position: relative; width: 975px; height: 1200px; }
  .poster {
    position: absolute; left: 57px; top: 0;
    width: 962px; height: 1340px;
    transform: scale(0.8955); transform-origin: top left;
    background: var(--paper);
  }
  .poster__field {
    position: absolute; left: 26px; top: 17px;
    width: 908px; height: 1196px;
    background: var(--forest);
  }
  .mission {
    position: absolute; right: 103px; top: 88px;
    text-align: right; color: var(--chalk);
  }
  .mission__line { display: block; line-height: 1; white-space: nowrap; }
  .mission__line--creating {
    font-family: "Jost", sans-serif; font-weight: 400;
    font-size: 126px; letter-spacing: 1px;
  }
  .mission__line--home {
    font-family: "Jost", sans-serif; font-weight: 400;
    font-size: 104px; margin-top: 8px;
  }
  .mission__for {
    font-family: "Playfair Display", serif; font-style: italic; font-weight: 400;
    font-size: 124px; letter-spacing: -2px;
  }
  .mission__line--abundant {
    font-family: "Playfair Display", serif; font-weight: 500;
    font-size: 106px; margin-top: 4px; letter-spacing: -1px;
  }
  .mission__line--life {
    font-family: "Playfair Display", serif; font-weight: 500;
    font-size: 96px; margin-top: 2px;
  }
  .values { position: absolute; left: 0; top: 0; width: 962px; height: 1340px; }
  .values__curve { fill: none; stroke: var(--chalk); stroke-width: 6; stroke-linecap: butt; }
  .values__badge { fill: var(--chalk); }
  .values__label {
    font-family: "Jost", sans-serif; font-weight: 400; font-size: 34px;
    fill: var(--chalk); text-anchor: middle; letter-spacing: 1px;
  }
  .footer {
    position: absolute; left: 90px; right: 73px; top: 1258px;
    display: flex; justify-content: space-between; align-items: center;
    color: var(--forest-ink);
  }
  .brand { display: flex; align-items: center; gap: 14px; }
  .brand__dot { width: 36px; height: 36px; border-radius: 50%; background: var(--forest-ink); }
  .brand__name {
    font-family: "Playfair Display", serif; font-weight: 500;
    font-size: 36px; letter-spacing: 5px;
  }
  .footer__url { font-family: "Jost", sans-serif; font-weight: 400; font-size: 31px; }
</style>
</head>
<body>
<div class="canvas">
  <div class="poster">
    <div class="poster__field"></div>

    <h1 class="mission">
      <span class="mission__line mission__line--creating">CREATING</span>
      <span class="mission__line mission__line--home">HOME<span class="mission__for">for</span></span>
      <span class="mission__line mission__line--abundant">ABUNDANT</span>
      <span class="mission__line mission__line--life">LIFE</span>
    </h1>

    <svg class="values" viewBox="0 0 962 1340" aria-label="Company values">
      <path class="values__curve" d="M277 688 A200 182 0 0 0 677 688"/>
      <path class="values__curve" d="M271 868 Q470 1020 632 909"/>
      <path class="values__curve" d="M714 833 L741 790"/>
      <path class="values__curve" d="M248 957 Q330 1005 424 1025"/>
      <path class="values__curve" d="M537 1027 Q580 1018 622 1002"/>

      <g class="value value--thinking">
        <circle class="values__badge" cx="474" cy="695" r="53"/>
        <circle cx="474" cy="690" r="24" fill="var(--bulb)" role="img" aria-label="Light bulb icon"/>
        <rect x="465" y="712" width="18" height="14" rx="3" fill="#4a4a4a"/>
        <text class="values__label" x="476" y="795">Thinking</text>
      </g>

      <g class="value value--love">
        <circle class="values__badge" cx="227" cy="828" r="53"/>
        <path d="M227 858 C205 842 193 830 193 814 C193 801 203 793 213 793 C220 793 225 797 227 803 C229 797 234 793 241 793 C251 793 261 801 261 814 C261 830 249 842 227 858 Z" fill="var(--heart)"/>
        <text class="values__label" x="224" y="915">Love</text>
      </g>

      <g class="value value--team">
        <circle class="values__badge" cx="683" cy="881" r="53"/>
        <circle cx="683" cy="881" r="28" fill="var(--team)" role="img" aria-label="Team member icon"/>
        <text class="values__label" x="680" y="972">Team</text>
      </g>

      <g class="value value--zoe">
        <circle class="values__badge" cx="480" cy="1043" r="53"/>
        <circle cx="480" cy="1043" r="36" fill="var(--smile)" role="img" aria-label="Joyful smiling emoji"/>
        <text class="values__label" x="477" y="1138">Zoe</text>
      </g>
    </svg>

    <footer class="footer">
      <div class="brand">
        <span class="brand__dot"></span>
        <span class="brand__name">VALDINTOR</span>
      </div>
      <span class="footer__url">valdintor.com.au</span>
    </footer>
  </div>
</div>
</body>
</html>
```